We (R. T. Galvin & Partners, Inc.) are an executive Search firm based in Los Angeles that is exclusively focused in the Med Tech and Health Tech arenas.   I need a logo to communicate that we are a high end search firm, but also that we are focused in the medicine and science arenas called health tech and med tech.  Many of our clients have robotics and artificial intelligence type products, so it is very technology forward.  I tend to gravitate towards clean, sharp aesthetic as opposed to something that is really over the top.
Attached are files with my logo in two different layouts.  In addition to the letterhead and envelope, I also will need an electronic letterhead in Microsoft Word.  I tend to
I look forward to seeing the designs and just let me know if you have any questions.
Dale

```html
<!DOCTYPE html>
<html lang="en">
<head>
<meta charset="utf-8">
<title>R. T. Galvin &amp; Partners, Inc. — Stationery</title>
<link href="https://fonts.googleapis.com/css2?family=Montserrat:wght@400;600&display=swap" rel="stylesheet">
<style>
  :root {
    --bg: #d9d9d9;
    --paper: #ffffff;
    --flap-grey: #e4e5e7;
    --brand-blue: #52a3da;
    --ink: #111111;
    --text-grey: #4a4a4a;
    --shadow: 2px 3px 4px rgba(0,0,0,0.35);
  }
  * { margin: 0; padding: 0; box-sizing: border-box; }
  html, body { width: 1200px; height: 859px; overflow: hidden; background: var(--bg); }
  body { position: relative; font-family: "Montserrat", sans-serif; color: var(--ink); }

  .sheet { position: absolute; background: var(--paper); box-shadow: var(--shadow); overflow: hidden; }

  .letterhead { left: 61px; top: 49px; width: 583px; height: 754px; }
  .envelope-back-grey { left: 688px; top: 50px; width: 450px; height: 279px; background: transparent; box-shadow: none; overflow: visible; }
  .envelope-back-blue { left: 687px; top: 353px; width: 452px; height: 212px; }
  .envelope-front { left: 687px; top: 587px; width: 452px; height: 213px; }

  .brand { position: absolute; display: flex; align-items: center; gap: 6px; }
  .brand-dot { width: 9px; height: 9px; border-radius: 50%; background: var(--brand-blue); flex: none; }
  .brand-name { font-weight: 600; color: var(--ink); line-height: 1.05; letter-spacing: 0.02em; }
  .brand-name span { display: block; }
  .brand-name .line-2 { letter-spacing: 0.22em; }

  .letterhead .brand { left: 40px; top: 88px; }
  .letterhead .brand-name .line-1 { font-size: 15px; }
  .letterhead .brand-name .line-2 { font-size: 6.5px; margin-top: 2px; }

  .contact { position: absolute; right: 40px; top: 42px; text-align: right; font-size: 8.8px; color: var(--text-grey); line-height: 11.6px; }
  .contact .gap { height: 6px; }
  .contact .row { display: flex; justify-content: flex-end; align-items: center; gap: 4px; }
  .contact svg { width: 6px; height: 6px; fill: none; stroke: var(--brand-blue); stroke-width: 1.2; }
  .accent-bar { position: absolute; right: 0; top: 43px; width: 7px; height: 70px; background: var(--brand-blue); }

  .wave { position: absolute; left: 0; bottom: 0; width: 100%; }
  .wave .fill-blue { fill: var(--brand-blue); }
  .wave .fill-ink { fill: var(--ink); }

  .flap { position: absolute; left: 0; top: 0; width: 100%; }
  .envelope-back-grey .body { position: absolute; left: 0; top: 67px; width: 450px; height: 212px; background: var(--paper); box-shadow: var(--shadow); }
  .envelope-back-grey .brand, .envelope-back-blue .brand { left: 50%; transform: translateX(-50%); }
  .envelope-back-grey .brand { top: 22px; }
  .envelope-back-blue .brand { top: 20px; }
  .envelope-back-blue .brand-dot { background: var(--paper); }
  .flap-brand .brand-name .line-1 { font-size: 12px; }
  .flap-brand .brand-name .line-2 { font-size: 5px; margin-top: 1px; }

  .envelope-front .brand { left: 23px; top: 22px; }
  .envelope-front .brand-name .line-1 { font-size: 12px; }
  .envelope-front .brand-name .line-2 { font-size: 5px; margin-top: 1px; }
  .return-address { position: absolute; left: 23px; top: 56px; font-size: 7px; line-height: 9px; color: var(--text-grey); }
</style>
</head>
<body>

<section class="sheet letterhead">
  <div class="brand">
    <div class="brand-name"><span class="line-1">R. T. GALVIN</span><span class="line-2">&amp; PARTNERS, INC.</span></div>
  </div>
  <address class="contact" style="font-style:normal">
    <div>418 Linden Court</div>
    <div>Westfield, CA 90211</div>
    <div class="gap"></div>
    <div class="row">+1 (310) 555-0148
      <svg viewBox="0 0 6 6"><path d="M1 0.5 L2 0.5 L2.5 2 L1.8 2.6 Q2.6 4 3.6 4.3 L4.2 3.6 L5.5 4.2 L5.5 5.4 Q2 5.6 0.6 1.2 Z"/></svg></div>
    <div class="row">+1 (310) 555-0172
      <svg viewBox="0 0 6 6"><rect x="0.6" y="2" width="4.8" height="2.4"/><rect x="1.6" y="0.6" width="2.8" height="1.4"/><rect x="1.6" y="4" width="2.8" height="1.4"/></svg></div>
    <div class="row">office@galvinpartners.com
      <svg viewBox="0 0 6 6"><rect x="0.6" y="1.2" width="4.8" height="3.6"/><path d="M0.6 1.2 L3 3.2 L5.4 1.2"/></svg></div>
    <div class="row">www.galvinpartners.com
      <svg viewBox="0 0 6 6"><circle cx="3" cy="3" r="2.4"/><ellipse cx="3" cy="3" rx="1" ry="2.4"/><path d="M0.6 3 H5.4"/></svg></div>
  </address>
  <div class="accent-bar"></div>
  <svg class="wave" viewBox="0 0 583 92" preserveAspectRatio="none" height="92" aria-hidden="true">
    <path class="fill-blue" d="M0 60 Q290 92 583 30 L583 92 L0 92 Z"/>
    <path class="fill-blue" d="M60 50 Q340 78 583 3 L583 15 Q340 82 60 50 Z"/>
    <path class="fill-ink" d="M0 44 Q270 84 495 55 Q270 76 0 55 Z"/>
  </svg>
</section>

<section class="sheet envelope-back-grey">
  <svg class="flap" viewBox="0 0 450 67" height="67" aria-hidden="true">
    <path d="M0 67 L20 8 Q23 0 32 0 L418 0 Q427 0 430 8 L450 67 Z" fill="var(--flap-grey)"/>
  </svg>
  <div class="body"></div>
  <div class="brand flap-brand">
    <div class="brand-dot"></div>
    <div class="brand-name"><span class="line-1">R. T. GALVIN</span><span class="line-2">&amp; PARTNERS, INC.</span></div>
  </div>
</section>

<section class="sheet envelope-back-blue">
  <svg class="flap" viewBox="0 0 452 66" height="66" aria-hidden="true">
    <path d="M0 0 L452 0 L434 56 Q431 66 420 66 L32 66 Q21 66 18 56 Z" fill="var(--brand-blue)"/>
  </svg>
  <div class="brand flap-brand">
    <div class="brand-dot"></div>
    <div class="brand-name"><span class="line-1">R. T. GALVIN</span><span class="line-2">&amp; PARTNERS, INC.</span></div>
  </div>
</section>

<section class="sheet envelope-front">
  <div class="brand">
    <div class="brand-dot"></div>
    <div class="brand-name"><span class="line-1">R. T. GALVIN</span><span class="line-2">&amp; PARTNERS, INC.</span></div>
  </div>
  <address class="return-address" style="font-style:normal">418 Linden Court<br>Westfield, CA 90211</address>
  <svg class="wave" viewBox="0 0 452 80" preserveAspectRatio="none" height="80" aria-hidden="true">
    <path class="fill-blue" d="M0 52 Q225 80 452 22 L452 80 L0 80 Z"/>
    <path class="fill-blue" d="M50 42 Q270 66 452 0 L452 10 Q270 70 50 42 Z"/>
    <path class="fill-ink" d="M0 37 Q210 74 385 47 Q210 66 0 47 Z"/>
  </svg>
</section>

</body>
</html>
```